Letterhead for Kembara Home Physician

Now we have a new logo we need some letterhead. Attached is the new logo and also the information we need to have on it. We have not yet decided on colour but would like to see a version in each to assist in choosing. I have attached one of the logos but do not have high quality version of the other 'ALGPS member' logo. These can be less prominent. Also Kembara Health Care Cooperative Inc. can be less prominent perhaps small font stating "KHP is trading name for the Kembara Health Care Cooperative Inc."

```html
<!DOCTYPE html>
<html lang="en">
<head>
<meta charset="utf-8">
<title>Kembara Home Physician – Letterhead</title>
<link href="https://fonts.googleapis.com/css2?family=Bitter:wght@400;700&display=swap" rel="stylesheet">
<style>
  :root {
    --ink: #111111;
    --band: #000000;
    --paper: #ffffff;
    --text: #1a1a1a;
    --muted: #333333;
    --member-green: #1f6b2a;
    --badge-blue: #1f4fa3;
    --badge-ring: #ffffff;
  }
  * { margin: 0; padding: 0; box-sizing: border-box; }
  html, body {
    width: 955px; height: 1200px; overflow: hidden;
    background: var(--paper);
    font-family: "Bitter", Georgia, serif;
    color: var(--text);
  }
  .letterhead { position: relative; width: 955px; height: 1200px; background: var(--paper); }

  .masthead {
    position: absolute; left: 0; top: 0; width: 955px; height: 133px;
    background: var(--band);
  }
  .masthead-rule {
    position: absolute; left: 0; top: 136px; width: 955px; height: 4px;
    background: var(--band);
  }
  .brand {
    position: absolute; left: 336px; top: 14px;
    display: flex; align-items: center; gap: 14px;
  }
  .brand-mark {
    width: 80px; height: 80px; border-radius: 50%;
    background: var(--paper);
  }
  .brand-name {
    color: var(--paper); font-weight: 700; font-size: 30px; line-height: 30px;
  }
  .trading-note {
    position: absolute; left: 0; width: 955px; top: 112px;
    text-align: center; color: var(--paper); font-size: 14px; line-height: 16px;
  }

  .footer-rule {
    position: absolute; left: 36px; top: 1077px; width: 892px; height: 2px;
    background: linear-gradient(to right, rgba(17,17,17,0.2), var(--ink) 15%, var(--ink) 85%, rgba(17,17,17,0.2));
  }
  .member-badge {
    position: absolute; left: 40px; top: 1126px; width: 50px; height: 44px;
    background: var(--member-green);
  }
  .member-caption {
    position: absolute; left: 15px; top: 1174px; width: 100px;
    text-align: center; font-size: 10px; line-height: 12px;
    white-space: nowrap; color: var(--muted);
  }
  .accreditation-badge {
    position: absolute; left: 133px; top: 1131px; width: 56px; height: 56px;
    border-radius: 50%; background: var(--badge-blue);
    box-shadow: inset 0 0 0 4px var(--badge-ring), 0 0 0 2px var(--badge-blue);
  }
  .contact {
    position: absolute; left: 200px; color: var(--text); white-space: nowrap;
    display: flex; align-items: center; gap: 6px;
  }
  .contact-address { top: 1098px; font-size: 18px; }
  .contact-lines { top: 1128px; font-size: 19px; }
  .contact-web { top: 1158px; font-size: 19px; }
  .contact .abn { font-size: 15px; }
  .contact .sep { color: var(--muted); }
  .icon { width: 17px; height: 17px; fill: var(--ink); flex: none; }
</style>
</head>
<body>
<div class="letterhead">
  <header class="masthead">
    <div class="brand">
      <div class="brand-mark"></div>
      <div class="brand-name">Kembara<br>Home<br>Physician</div>
    </div>
    <p class="trading-note">KHP is trading name for the Kembara Health Care Cooperative Inc.</p>
  </header>
  <div class="masthead-rule"></div>

  <footer>
    <div class="footer-rule"></div>
    <div class="member-badge" role="img" aria-label="ALGPS member badge"></div>
    <div class="member-caption">ALGPS MEMBER</div>
    <div class="accreditation-badge" role="img" aria-label="Accreditation badge"></div>

    <p class="contact contact-address">4/18 Harbour Crest Road Kembara NSW 2590 <span class="sep">|</span> PO Box 377, Linden Vale NSW 2594</p>

    <p class="contact contact-lines">
      <svg class="icon" viewBox="0 0 24 24" aria-hidden="true"><path d="M6.6 10.8a15.1 15.1 0 0 0 6.6 6.6l2.2-2.2a1 1 0 0 1 1-.25 11.4 11.4 0 0 0 3.6.57 1 1 0 0 1 1 1V20a1 1 0 0 1-1 1A17 17 0 0 1 3 4a1 1 0 0 1 1-1h3.5a1 1 0 0 1 1 1c0 1.25.2 2.45.57 3.57a1 1 0 0 1-.25 1z"/></svg>
      02 4310 7284 <span class="sep">|</span>
      <svg class="icon" viewBox="0 0 24 24" aria-hidden="true"><path d="M5 11l1.6-4.6A2 2 0 0 1 8.5 5h7a2 2 0 0 1 1.9 1.4L19 11a2 2 0 0 1 2 2v5h-2v2h-3v-2H8v2H5v-2H3v-5a2 2 0 0 1 2-2zm2.2 0h9.6l-1.2-3.5H8.4zM6.5 16a1.5 1.5 0 1 0 0-3 1.5 1.5 0 0 0 0 3zm11 0a1.5 1.5 0 1 0 0-3 1.5 1.5 0 0 0 0 3z"/></svg>
      02 4310 7291 <span class="sep">|</span>
      <svg class="icon" viewBox="0 0 24 24" aria-hidden="true"><path d="M3 6h18v12H3zm2 2v.5l7 4.5 7-4.5V8zm0 2.9V16h14v-5.1l-7 4.5z"/></svg>
      enquiries@kembarahp.com.au
    </p>

    <p class="contact contact-web">
      <span class="abn">ABN&nbsp; 48 319 552 107</span> <span class="sep">|</span>
      <svg class="icon" viewBox="0 0 24 24" aria-hidden="true"><path d="M12 2a10 10 0 1 0 0 20 10 10 0 0 0 0-20zm6.9 9h-3a15 15 0 0 0-1.2-5.6A8 8 0 0 1 18.9 11zM12 4.1c.9 1.2 1.700 3.6 1.900 6.900h-3.800c.2-3.300 1-5.700 1.900-6.900zM9.3 5.4A15 15 0 0 0 8.1 11h-3a8 8 0 0 1 4.2-5.6zM5.1 13h3a15 15 0 0 0 1.2 5.6A8 8 0 0 1 5.1 13zm6.9 6.9c-.9-1.2-1.7-3.6-1.9-6.9h3.8c-.2 3.3-1 5.7-1.9 6.9zm2.7-1.3a15 15 0 0 0 1.2-5.6h3a8 8 0 0 1-4.2 5.6z"/></svg>
      www.kembarahp.com.au
    </p>
  </footer>
</div>
</body>
</html>
```